Podiatry clinic requires a modern revamp and editing of existing website.

I would like a fresh new look and updated information for my current business website. An easy to navigate site with prominent address and phone number for call to action. We are a podiatry clinic that focuses on general and sports podiatry.
I would like 4 pages; including Home page, About Us, Services & Contact.
www.brambleridgepodiatry.net

Target Market(s)

Active working professionals.

Industry/Entity Type

Medical

Coding

Coded - Design and coding required

Number of Pages Required

4 page

Font styles to use
Sans Serif

Colors
6b449b

Requirements
Must have
• A modern look with logo and active images; clean and uncluttered. Visible phone number and address for call to action.
• 4 pages - Home, About Us, Services, Contact.
• Home page - update address & service logos.
• About Us - update of personal information.
• Services - Revamp of existing page.
• Contact page to include Google map, email & phone number.
Nice to have
• Ability to add content easily; eg. a blog or adding video onto Home page.
• Link to social link circle page.

```html
<!DOCTYPE html>
<html lang="en">
<head>
<meta charset="utf-8">
<title>Bramble Ridge Podiatry – Contact</title>
<link rel="stylesheet" href="https://fonts.googleapis.com/css2?family=Roboto+Condensed:wght@300;400&family=Raleway:wght@400;500;600&family=Open+Sans:wght@400;600&display=swap">
<style>
:root{
  --purple:#6b449b;
  --nav:#4a3296;
  --navy:#3b2f8f;
  --green:#7cc242;
  --grey:#4a4a4a;
  --line:#c9c9c9;
  --white:#ffffff;
}
*{box-sizing:border-box;margin:0;padding:0}
html,body{width:817px;height:1200px;overflow:hidden;background:var(--white)}
body{position:relative;font-family:"Open Sans",sans-serif;color:var(--grey)}
.hero{position:absolute;left:0;top:0;width:817px;height:461px;
  background:linear-gradient(180deg,#5a4f5c 0%,#b5735a 18%,#d69a6a 28%,#5e5048 45%,#3a3433 70%,#2c2a2b 100%);}
.hero-photo{position:absolute;inset:0}
.brand{position:absolute;left:56px;top:40px;display:flex;align-items:center;gap:8px;
  font-family:"Raleway",sans-serif;font-weight:600;font-size:18px;color:var(--white)}
.brand-dot{width:14px;height:14px;border-radius:50%;background:var(--purple)}
.top-contact{position:absolute;right:58px;top:30px;text-align:right;
  font-family:"Roboto Condensed",sans-serif;font-weight:300;color:var(--white);font-size:15px;line-height:32px}
.top-contact svg{vertical-align:-3px;margin-right:5px}
.top-contact strong{font-weight:400}
.hero-title{position:absolute;left:0;width:817px;top:170px;text-align:center;
  font-family:"Roboto Condensed",sans-serif;font-weight:400;font-size:56px;color:var(--white)}
.hero-rule{position:absolute;left:282px;top:248px;width:248px;height:1px;background:rgba(255,255,255,.8)}
.hero-sub{position:absolute;left:0;width:817px;top:262px;text-align:center;
  font-family:"Roboto Condensed",sans-serif;font-weight:300;font-size:29px;color:var(--white)}
.btn-book{position:absolute;left:322px;top:317px;width:169px;height:35px;background:var(--purple);
  color:var(--white);font-family:Arial,sans-serif;font-size:12px;display:flex;align-items:center;justify-content:center;border-radius:2px}
.nav{position:absolute;left:0;top:461px;width:817px;height:41px;background:var(--nav);display:flex;padding-left:53px}
.nav a{display:flex;align-items:center;padding:0 22px;color:var(--white);text-decoration:none;
  font-family:"Raleway",sans-serif;font-size:13px;margin-right:6px}
.nav a.active{background:var(--green)}
.section-title{position:absolute;left:0;width:817px;text-align:center;font-family:"Raleway",sans-serif;
  font-weight:400;font-size:29px;color:var(--grey)}
.section-title span{color:var(--navy)}
.clinic-name{position:absolute;left:54px;top:598px;font-family:"Raleway",sans-serif;font-size:22px;color:var(--navy)}
.details{position:absolute;left:56px;top:642px;font-size:11px;line-height:16px;color:var(--grey)}
.details li{list-style:none;display:flex;gap:11px;margin-bottom:12px}
.details svg{flex:0 0 14px;margin-top:1px}
.details .phone{font-weight:600}
.social{position:absolute;left:53px;top:744px;width:31px;height:31px;border-radius:50%;background:var(--nav)}
.map{position:absolute;left:374px;top:598px;width:390px;height:199px;border:1px solid var(--nav);padding:3px;background:var(--white)}
.map div{width:100%;height:100%;background:linear-gradient(135deg,#f3e6c8,#e9ddc2 50%,#f1e4c6)}
.form{position:absolute;left:231px;top:884px;width:355px}
.field{height:35px;border:1px solid var(--line);border-radius:3px;margin-bottom:4px;
  font-family:Arial,sans-serif;font-size:10px;color:#888;padding:11px 11px}
.field.message{height:70px}
.btn-submit{position:absolute;left:352px;top:1083px;width:113px;height:35px;border-radius:18px;background:var(--purple);
  color:var(--white);font-family:"Raleway",sans-serif;font-weight:600;font-size:16px;display:flex;align-items:center;justify-content:center}
.footer{position:absolute;left:0;top:1165px;width:817px;height:35px;background:var(--nav);color:var(--white);
  font-size:11px;display:flex;align-items:center;justify-content:center}
</style>
</head>
<body>
<header class="hero">
  <div class="hero-photo" role="img" aria-label="Runner's legs on an open road at sunset"></div>
  <div class="brand"><span class="brand-dot"></span>Bramble Ridge Podiatry</div>
  <div class="top-contact">
    <div><svg width="12" height="16" viewBox="0 0 12 16"><path d="M6 0a6 6 0 0 0-6 6c0 4.5 6 10 6 10s6-5.5 6-10a6 6 0 0 0-6-6zm0 8.5A2.5 2.5 0 1 1 6 3.5a2.5 2.5 0 0 1 0 5z" fill="#fff"/></svg>Suite 12 / 88 Harrow Lane Ashford 4021</div>
    <div><svg width="18" height="18" viewBox="0 0 24 24"><path d="M6.6 10.8a15.1 15.1 0 0 0 6.6 6.6l2.2-2.2c.3-.3.7-.4 1-.2 1.1.4 2.3.6 3.6.6.6 0 1 .4 1 1V20c0 .6-.4 1-1 1A17 17 0 0 1 3 4c0-.6.4-1 1-1h3.5c.6 0 1 .4 1 1 0 1.3.2 2.5.6 3.6.1.3 0 .7-.2 1z" fill="#fff"/></svg>CALL US NOW : <strong>1300 555 204</strong></div>
  </div>
  <h1 class="hero-title">Don't let pain run your life</h1>
  <div class="hero-rule"></div>
  <p class="hero-sub">Choose to be pain free</p>
  <a class="btn-book">BOOK AN APPOINTMENT</a>
</header>

<nav class="nav">
  <a class="active">HOME</a><a>ABOUT</a><a>SERVICES</a><a>CONTACT</a>
</nav>

<h2 class="section-title" style="top:538px">CONTACT <span>US</span></h2>
<h3 class="clinic-name">BRAMBLE RIDGE PODIATRY</h3>
<ul class="details">
  <li><svg width="14" height="16" viewBox="0 0 12 16"><path d="M6 0a6 6 0 0 0-6 6c0 4.5 6 10 6 10s6-5.5 6-10a6 6 0 0 0-6-6zm0 8.5A2.5 2.5 0 1 1 6 3.5a2.5 2.5 0 0 1 0 5z" fill="#4a3296"/></svg><span>Suite 12 / 88 Harrow Lane<br>Ashford 4021.</span></li>
  <li><svg width="14" height="14" viewBox="0 0 24 24"><path d="M6.6 10.8a15.1 15.1 0 0 0 6.6 6.6l2.2-2.2c.3-.3.7-.4 1-.2 1.1.4 2.3.6 3.6.6.6 0 1 .4 1 1V20c0 .6-.4 1-1 1A17 17 0 0 1 3 4c0-.6.4-1 1-1h3.5c.6 0 1 .4 1 1 0 1.3.2 2.5.6 3.6.1.3 0 .7-.2 1z" fill="#4a3296"/></svg><span class="phone">1300 555 204</span></li>
  <li><svg width="14" height="12" viewBox="0 0 14 12"><rect x="0.75" y="0.75" width="12.5" height="10.5" rx="1" fill="none" stroke="#4a3296" stroke-width="1.5"/><path d="M1 1.5l6 5 6-5" fill="none" stroke="#4a3296" stroke-width="1.5"/></svg><span>info@brambleridgepodiatry.net</span></li>
</ul>
<div class="social" role="img" aria-label="Social page link"></div>
<div class="map"><div role="img" aria-label="Street map showing the clinic location"></div></div>

<h2 class="section-title" style="top:833px">GET IN <span>TOUCH WITH US</span></h2>
<form class="form">
  <div class="field">Name</div>
  <div class="field">E-Mail</div>
  <div class="field">Phone</div>
  <div class="field message">Message</div>
</form>
<div class="btn-submit">SUBMIT</div>

<footer class="footer">© Bramble Ridge Podiatry- 2016. All Rights Reserved.</footer>
</body>
</html>
```